Deskside Thrive Fliers and logo design

We need to design a product logo and some informational fliers for a vigour quest.
I have attached our Deskside Thrive logo - colours need to be complimentary but not the same, we would like fresh, funky but still professional. We generally communicate in a fairly casual way to reach our market. (We don't like boring)
Clear and simple - not too busy
images are good but not actual photos
Here is our website to give you an idea www.desksidethrive.co.nz
The flier is a 3 page document.
The logo is to say Vigour Quest. The challenge is based on exercise, connecting with people, giving, learning and taking notice (The 7 paths to flourishing) Once agin the logo needs to be complementary but not the same.
The Deskside thrive logo needs to be on the fliers but the vigour quest logo is separate.
Thanks very much!!

```html
<!DOCTYPE html>
<html lang="en">
<head>
<meta charset="utf-8">
<title>Deskside Thrive – Flier</title>
<link href="https://fonts.googleapis.com/css2?family=Montserrat:wght@500;700;900&family=Open+Sans:wght@400;600;700&display=swap" rel="stylesheet">
<style>
  :root{
    --teal:#3aa98c;
    --teal-dark:#2b8a70;
    --ink:#141414;
    --maroon:#8a3a3f;
    --red:#d7282f;
    --paper:#ffffff;
    --stage:#e6e6e6;
    --pattern-a:#f4f4f4;
    --pattern-b:#e2e2e2;
    --parch-a:#f3d9a4;
    --parch-b:#c9924b;
  }
  *{box-sizing:border-box;margin:0;padding:0}
  html,body{width:1200px;height:720px;overflow:hidden}
  body{background:var(--stage);font-family:"Open Sans",sans-serif;position:relative}

  .page{position:absolute;top:40px;width:460px;height:640px;background:var(--paper);
        box-shadow:0 6px 18px rgba(0,0,0,.12);overflow:hidden}
  .page--cover{left:120px}
  .page--tips{left:620px}
  .page::after{content:"";position:absolute;left:0;right:0;bottom:0;height:7px;background:var(--maroon)}

  .icon-field{position:absolute;left:0;top:0;width:100%;height:300px;
      background:linear-gradient(180deg,var(--pattern-b),var(--pattern-a) 70%,var(--paper))}

  .title-block{position:absolute;left:34px;top:300px;width:400px;transform:rotate(-4deg)}
  .title-flag{position:absolute;left:10px;top:4px;width:300px;height:30px}
  .title-kicker{position:relative;display:block;margin-left:78px;font-family:"Montserrat",sans-serif;
      font-weight:900;font-size:24px;letter-spacing:1px;color:var(--ink)}
  .title-main{display:block;font-family:"Montserrat",sans-serif;font-weight:900;font-size:62px;
      line-height:1;letter-spacing:1px;color:var(--ink)}
  .title-ribbon{position:relative;margin-top:14px;margin-left:26px;width:360px;background:var(--teal);
      color:#fff;font-size:10.5px;line-height:1.35;padding:10px 16px}
  .title-ribbon::before{content:"";position:absolute;left:0;bottom:-12px;border-top:12px solid var(--teal-dark);
      border-left:18px solid transparent}

  .brand{position:absolute;bottom:26px;display:flex;align-items:center;gap:8px;
      font-family:"Montserrat",sans-serif;font-weight:700;font-size:15px}
  .brand--thrive{left:30px;color:var(--teal)}
  .brand--quest{right:30px;color:var(--ink)}
  .brand__dot{width:14px;height:14px;border-radius:50%}
  .brand--thrive .brand__dot{background:var(--teal)}
  .brand--quest .brand__dot{background:var(--red)}

  .tips-field{position:absolute;left:0;right:0;bottom:0;height:220px;
      background:linear-gradient(0deg,var(--pattern-b),var(--paper))}
  .scroll{position:absolute;left:30px;top:40px;width:400px;height:500px;border-radius:10px;
      background:linear-gradient(135deg,var(--parch-a),#e8bf7a 55%,var(--parch-b))}
  .tips{position:absolute;left:58px;top:66px;width:344px;color:#3b2a14}
  .tips__title{font-family:"Montserrat",sans-serif;font-weight:700;font-size:18px;color:#fff;
      background:#a86b2c;padding:6px 12px;margin-bottom:14px;text-align:center}
  .tips__intro{font-size:12px;line-height:1.5;margin-bottom:10px}
  .tips__list{font-size:12px;line-height:1.55;padding-left:18px}
  .tips__close{font-size:12px;font-weight:700;margin-top:10px}
</style>
</head>
<body>

<section class="page page--cover">
  <div class="icon-field" role="img" aria-label="Soft grey tile pattern of small wellbeing icons: briefcase, heart, smiley face, runner, money bag"></div>

  <div class="title-block">
    <svg class="title-flag" viewBox="0 0 300 30" aria-hidden="true">
      <polygon points="0,30 40,0 300,0 300,30" fill="var(--teal)"/>
    </svg>
    <span class="title-kicker">DESKSIDE</span>
    <span class="title-main">THRIVE</span>
    <p class="title-ribbon">Programmes, initiatives and events developed to optimise wellbeing, personal development, workplace culture, job satisfaction, engagement, organisational commitment and to assist with change management.</p>
  </div>

  <div class="brand brand--thrive"><span class="brand__dot"></span>Deskside thrive</div>
  <div class="brand brand--quest"><span class="brand__dot"></span>Vigour Quest</div>
</section>

<section class="page page--tips">
  <div class="tips-field" role="img" aria-label="Faint grey tile pattern of small wellbeing icons"></div>
  <div class="scroll" role="img" aria-label="Illustrated parchment scroll with wooden rollers"></div>

  <div class="tips">
    <h2 class="tips__title">10 tips to improve your wellbeing</h2>
    <p class="tips__intro">You do not need big changes to feel better at work. Small steps add up over time, so pick one idea and start today.</p>
    <ol class="tips__list">
      <li>Take a short walk at lunch.</li>
      <li>Drink water through the day.</li>
      <li>Say hello to someone new.</li>
      <li>Stretch at your desk each hour.</li>
      <li>Learn one new thing this week.</li>
      <li>Thank a colleague for their help.</li>
      <li>Step outside and notice the sky.</li>
      <li>Plan a screen-free evening.</li>
      <li>Share a healthy snack with your team.</li>
      <li>Get to bed a little earlier.</li>
    </ol>
    <p class="tips__close">Keep going and enjoy the journey.</p>
  </div>

  <div class="brand brand--quest"><span class="brand__dot"></span>Vigour Quest</div>
</section>

</body>
</html>
```